I need a business card design for a new business based in South West Australia.
I specialize in residential window cleaning & general handyman maintenance.

Dale Marsh - 412 SILVER HAWK DETAILING
- Window Cleaning
- House Maintenance

```html
<!DOCTYPE html>
<html lang="en">
<head>
<meta charset="utf-8">
<title>412 Silver Hawk Detailing – Business Card</title>
<link rel="stylesheet" href="https://fonts.googleapis.com/css2?family=Open+Sans:wght@400;600&display=swap">
<style>
  :root {
    --backdrop: #d9d4cc;
    --card-frost-top: #f1f0ee;
    --card-frost-bottom: #dcdfe6;
    --band-blue: #2d3f86;
    --band-blue-deep: #1d2a66;
    --rail-grey: #6a6a6c;
    --title-ink: #1b1b1c;
    --rose-gold: #e9cabd;
    --rose-gold-soft: #cdb0a4;
  }
  html, body {
    margin: 0;
    padding: 0;
    width: 1200px;
    height: 970px;
    overflow: hidden;
    background: var(--backdrop);
  }
  .canvas {
    position: relative;
    width: 1200px;
    height: 970px;
  }
  .card {
    position: absolute;
    left: 65px;
    top: 165px;
    width: 1070px;
    height: 640px;
    background: linear-gradient(180deg, var(--card-frost-top), var(--card-frost-bottom));
    box-shadow: 0 18px 40px rgba(0,0,0,0.18);
    overflow: hidden;
  }
  .card-shapes {
    position: absolute;
    inset: 0;
  }
  .company-name {
    position: absolute;
    left: 0;
    right: 0;
    top: 115px;
    margin: 0;
    text-align: center;
    font-family: "Open Sans", sans-serif;
    font-weight: 600;
    font-size: 57px;
    letter-spacing: 0.5px;
    color: var(--title-ink);
  }
  .person-name {
    position: absolute;
    right: 620px;
    top: 445px;
    margin: 0;
    font-family: "Open Sans", sans-serif;
    font-weight: 400;
    font-size: 46px;
    color: var(--rose-gold);
  }
  .divider {
    position: absolute;
    left: 501px;
    top: 372px;
    width: 2px;
    height: 222px;
    background: linear-gradient(180deg, rgba(233,202,189,0.2), var(--rose-gold), rgba(233,202,189,0.2));
  }
  .services {
    position: absolute;
    left: 545px;
    top: 438px;
    margin: 0;
    padding: 0;
    list-style: none;
    font-family: "Open Sans", sans-serif;
    font-size: 31px;
    color: var(--rose-gold-soft);
  }
  .service {
    display: flex;
    align-items: center;
    height: 48px;
    margin-bottom: 10px;
  }
  .service-dot {
    width: 14px;
    height: 14px;
    border-radius: 50%;
    background: var(--rose-gold-soft);
    margin: 0 38px 0 10px;
  }
</style>
</head>
<body>
  <main class="canvas">
    <section class="card">
      <svg class="card-shapes" width="1070" height="640" viewBox="0 0 1070 640" aria-hidden="true">
        <defs>
          <linearGradient id="bandFill" x1="0" y1="0" x2="0" y2="1">
            <stop offset="0" stop-color="var(--band-blue)"/>
            <stop offset="1" stop-color="var(--band-blue-deep)"/>
          </linearGradient>
        </defs>
        <polygon class="blue-band" points="0,237 130,312 945,312 1070,242 1070,640 0,640" fill="url(#bandFill)"/>
        <polygon class="grey-rail" points="53,256 130,287 945,287 1023,256 945,300 130,300" fill="var(--rail-grey)"/>
      </svg>
      <h1 class="company-name">412 SILVER HAWK DETAILING</h1>
      <p class="person-name">Dale Marsh</p>
      <div class="divider"></div>
      <ul class="services">
        <li class="service"><span class="service-dot"></span>Window Cleaning</li>
        <li class="service"><span class="service-dot"></span>House Maintenance</li>
      </ul>
    </section>
  </main>
</body>
</html>
```